Modern Medical Optometry Website

We need mordern, Patient friendly website. Easy to navigate and enhance our advance medical technology and excellent patient care.
1. HOME PAGE
2. OUR TEAM PAGE
3. EYECARE PAGE - VISION SERVICES, EYE EXAMS, KERATOCONUS CENTER, GLAUCOMA , DIABITES, MELORIDEX EXAM, DIGITAL RETINAL, OCT.
4. MYOPIA CONTROL CLINIC
5. DRY EYE CLINIC
6. EYEWEAR
7. PATIENT CENTER - BLOG
7. CONTACT US
This is our current website www.brivaloka.com
and We want to add more content and a cleaner design like these website
http://tarnwickfolvendale.com/
https://www.qmvorlu.com/

```html
<!DOCTYPE html>
<html lang="en">
<head>
<meta charset="utf-8">
<title>Lumora Optometry</title>
<link href="https://fonts.googleapis.com/css2?family=Oswald:wght@400;500&family=Lato:wght@400;700;900&display=swap" rel="stylesheet">
<style>
:root{
  --yellow:#f2c318;
  --blue:#1f6fc0;
  --ink:#222;
  --text:#444;
  --grey-bg:#f1f1f1;
  --dark:#262626;
  --white:#fff;
}
*{box-sizing:border-box;margin:0;padding:0}
html,body{width:1200px;height:3371px;overflow:hidden}
body{font-family:"Lato",sans-serif;color:var(--text);background:var(--white)}
.heading{font-family:"Oswald",sans-serif;font-weight:400;color:var(--ink);text-transform:uppercase;text-align:center;font-size:40px}
.btn{display:inline-block;background:var(--yellow);color:var(--white);font-family:"Oswald",sans-serif;font-size:19px;padding:8px 30px;text-decoration:none}

/* header */
.site-header{height:144px;position:relative}
.brand{position:absolute;left:85px;top:20px;display:flex;align-items:center;gap:12px}
.brand-mark{width:40px;height:40px;background:var(--yellow)}
.brand-name{font-family:"Lato",sans-serif;font-weight:400;font-size:16px;color:#555;text-transform:uppercase;letter-spacing:1px}
.call{position:absolute;left:675px;top:44px}
.call-label{font-weight:900;font-size:15px;color:var(--ink)}
.call-number{font-size:28px;color:var(--yellow);font-weight:400}
.appt{position:absolute;left:884px;top:49px;width:241px;height:46px;background:#222;color:var(--white);font-weight:700;font-size:15px;display:flex;align-items:center;justify-content:center;text-transform:uppercase}

.main-nav{height:52px;background:var(--blue);display:flex;align-items:center;padding-left:86px}
.main-nav a{color:var(--white);text-decoration:none;font-weight:700;font-size:14px;text-transform:uppercase;margin-right:38px}

/* hero */
.hero{height:516px;position:relative;background:linear-gradient(180deg,#7b6a58 0%,#8f7a62 45%,#6e5238 100%)}
.hero-title{position:absolute;top:160px;width:100%;text-align:center;color:var(--white);font-family:"Lato",sans-serif;font-weight:900;font-size:76px}
.hero-sub{position:absolute;top:248px;width:100%;text-align:center;color:var(--white);font-size:28px}
.dots{position:absolute;top:468px;left:565px;display:flex;gap:10px}
.dots span{width:10px;height:10px;border-radius:50%;background:var(--white)}
.dots span:first-child{background:var(--yellow)}

/* welcome */
.welcome{height:393px;text-align:center;padding-top:50px}
.welcome .promise{color:var(--yellow);font-weight:700;font-size:24px;margin:22px 0 14px}
.welcome p{width:990px;margin:0 auto;font-size:16px;line-height:32px}
.welcome .btn{margin-top:26px}

/* eyecare */
.eyecare{height:778px;background:var(--grey-bg);position:relative;padding-top:52px}
.tiles{position:absolute;left:74px;top:137px;display:grid;grid-template-columns:repeat(3,331px);gap:30px 29px}
.tile{height:231px;display:flex;align-items:center;justify-content:center;color:var(--white);font-family:"Oswald",sans-serif;font-size:28px;text-transform:uppercase}
.eyecare .btn{position:absolute;top:672px;left:528px}

/* reviews */
.reviews{height:463px;background:linear-gradient(180deg,#2f2a25,#3a3128);position:relative;padding-top:54px}
.reviews .heading{color:var(--white)}
.quotes{display:flex;justify-content:center;gap:58px;margin-top:26px}
.quote{width:300px;text-align:center;color:var(--white);font-size:15px;line-height:25px}
.quote .who{color:var(--yellow);font-weight:900;margin-top:20px}
.stars{letter-spacing:4px;font-size:16px}
.reviews-btn{position:absolute;top:354px;left:512px;font-size:18px;padding:8px 24px}

/* patient center */
.patient{height:638px;position:relative;padding-top:52px}
.posts{position:absolute;left:164px;top:136px;display:flex;gap:26px}
.post{width:423px}
.post-image{height:207px}
.post h3{font-family:"Oswald",sans-serif;font-weight:400;font-size:28px;color:var(--ink);margin:36px 0 10px}
.post p{font-size:15px;line-height:27px;margin-bottom:24px;color:#444}
.arrow{position:absolute;top:346px}

/* footer */
.site-footer{height:387px;background:var(--dark);position:relative;color:#ccc}
.site-footer h2{font-family:"Oswald",sans-serif;font-weight:400;color:var(--white);font-size:30px;text-transform:uppercase;position:absolute;top:32px}
.office{position:absolute;top:96px;font-size:13px;line-height:24px}
.office strong{color:var(--yellow);font-weight:900;font-size:13px;text-transform:uppercase;display:block}
.office .row{display:flex;align-items:center;gap:12px}
.map{position:absolute;left:533px;top:99px;width:289px;height:171px;background:linear-gradient(135deg,#e4e2dc,#d6e2cd)}
.hours{position:absolute;left:863px;top:96px;font-size:13px;line-height:34px}
.hours .row{display:flex}
.hours .row span:first-child{width:168px}
.hours .note{line-height:24px;margin-top:4px}
.rule{position:absolute;left:74px;right:74px;top:323px;height:1px;background:#3b3b3b}
.copyright{position:absolute;left:74px;top:340px;font-size:11px;color:#888}
.social{position:absolute;left:938px;top:336px;display:flex;gap:14px}
.social span{width:24px;height:24px;border-radius:50%;background:#777}
</style>
</head>
<body>

<header class="site-header">
  <div class="brand"><span class="brand-mark"></span><span class="brand-name">Lumora Optometry</span></div>
  <div class="call">
    <div class="call-label">CALL OR TEXT US</div>
    <div class="call-number">818-555-0142</div>
  </div>
  <div class="appt">Make an Appointment</div>
</header>

<nav class="main-nav">
  <a>Home</a><a>Our Team</a><a>Eyecare</a><a>Myopia Control Clinic</a><a>Dry Eye Clinic</a><a>Eyewear</a><a>Patient Center</a><a>Contact Us</a>
</nav>

<section class="hero" role="img" aria-label="Photo of the optometry clinic interior with eyewear displays">
  <h1 class="hero-title">LUMORA OPTOMETRY</h1>
  <div class="hero-sub">Etiam elementum est id sapien tincidunt.</div>
  <div class="dots"><span></span><span></span><span></span><span></span></div>
</section>

<section class="welcome">
  <h2 class="heading">Welcome to our website</h2>
  <div class="promise">THE LUMORA PROMISE</div>
  <p>Welcome to Lumora Optometry, where your vision and eye health are our sole priority. We take great pride in providing you with state-of-the-art eyecare matched with personal attention from our staff and doctors. Your quality of life is our goal and we believe that healthy eyesight is vital to achieving it.</p>
  <a class="btn">Read More</a>
</section>

<section class="eyecare">
  <h2 class="heading">Eyecare</h2>
  <div class="tiles">
    <div class="tile" role="img" aria-label="Optical shop with eyewear frames" style="background:linear-gradient(135deg,#4a3e36,#6b5c50)">Vision Services</div>
    <div class="tile" role="img" aria-label="Eye exam with a slit lamp" style="background:linear-gradient(135deg,#8a6a2a,#b08a3a)">Eye Exams</div>
    <div class="tile" role="img" aria-label="Corneal topography equipment" style="background:linear-gradient(135deg,#6b6363,#8c7b7b)">Keratoconus Center</div>
    <div class="tile" role="img" aria-label="Glaucoma consultation" style="background:linear-gradient(135deg,#6a6e72,#8d7f78)">Glaucoma</div>
    <div class="tile" role="img" aria-label="Close-up of an eye" style="background:linear-gradient(135deg,#3a2e28,#5a4a3e)">Diabites</div>
    <div class="tile" role="img" aria-label="Retinal imaging graphic" style="background:linear-gradient(135deg,#56585a,#7a7c7e)">Meloridex Exam</div>
  </div>
  <a class="btn">View All Services</a>
</section>

<section class="reviews" role="img" aria-label="Background photo of a patient trying on eyewear">
  <h2 class="heading">Customer Reviews</h2>
  <div class="quotes">
    <div class="quote">“Lorem ipsum dolor sit amet, consectetur adipiscing elit. Proin a libero tortornunc tellus lectus, iaculis vitae scelerisque rutrum, mattis ac nibh. ..”<div class="who">DR. WREN</div><div class="stars">★★★★★</div></div>
    <div class="quote">“Lorem ipsum dolor sit amet, consectetur adipiscing elit. Proin a libero tortornunc tellus lectus, iaculis vitae scelerisque rutrum, mattis ac nibh. ..”<div class="who">DR. WREN</div><div class="stars">★★★★★</div></div>
    <div class="quote">“Lorem ipsum dolor sit amet, consectetur adipiscing elit. Proin a libero tortornunc tellus lectus, iaculis vitae scelerisque rutrum, mattis ac nibh. ..”<div class="who">DR. WREN</div><div class="stars">★★★★★</div></div>
  </div>
  <a class="btn reviews-btn">Read All Reviews</a>
</section>

<section class="patient">
  <h2 class="heading">Patient Center</h2>
  <svg class="arrow" style="left:95px" width="16" height="30" viewBox="0 0 16 30"><path d="M14 2 2 15l12 13" fill="none" stroke="#555" stroke-width="2"/></svg>
  <div class="posts">
    <article class="post">
      <div class="post-image" role="img" aria-label="Group photo of clinic staff" style="background:linear-gradient(135deg,#9a8a7a,#5a4a44)"></div>
      <h3>DUIS SIT AMET BIBENDUM</h3>
      <p>Curabitur volutpat et nisl et euismod. Sed at sollicitudin dolor. Sed vitae lorem vitae turpis malesuada faucibus vitae sit amet magna.</p>
      <a class="btn">Read More</a>
    </article>
    <article class="post">
      <div class="post-image" role="img" aria-label="Doctor examining a patient" style="background:linear-gradient(135deg,#7a4a30,#3a2a24)"></div>
      <h3>DUIS SIT AMET BIBENDUM</h3>
      <p>Curabitur volutpat et nisl et euismod. Sed at sollicitudin dolor. Sed vitae lorem vitae turpis malesuada faucibus vitae sit amet magna.</p>
      <a class="btn">Read More</a>
    </article>
  </div>
  <svg class="arrow" style="left:1088px" width="16" height="30" viewBox="0 0 16 30"><path d="M2 2l12 13L2 28" fill="none" stroke="#555" stroke-width="2"/></svg>
</section>

<footer class="site-footer">
  <h2 style="left:74px">Contact Info</h2>
  <div class="office" style="left:74px">
    <strong>Lumora Optometry</strong>
    4120 Alderbrook Ave, Ashgrove<br>CA 90210
    <div class="row"><svg width="12" height="12" viewBox="0 0 12 12"><path d="M2 1h3l1 3-2 1a7 7 0 0 0 3 3l1-2 3 1v3c-6 0-9-3-9-9z" fill="#f2c318"/></svg>818-555-0142</div>
    <div class="row"><svg width="12" height="10" viewBox="0 0 12 10"><rect width="12" height="10" fill="#f2c318"/><path d="M0 0l6 5 6-5" fill="none" stroke="#262626"/></svg>info@brivaloka.com</div>
  </div>
  <div class="office" style="left:290px">
    <strong>Canyon Ridge</strong>
    2290 Quillan St.,<br>Suite 4, Canyon Ridge, CA 90211
    <div class="row"><svg width="12" height="12" viewBox="0 0 12 12"><path d="M2 1h3l1 3-2 1a7 7 0 0 0 3 3l1-2 3 1v3c-6 0-9-3-9-9z" fill="#f2c318"/></svg>818-555-0187</div>
    <div class="row"><svg width="12" height="10" viewBox="0 0 12 10"><rect width="12" height="10" fill="#f2c318"/><path d="M0 0l6 5 6-5" fill="none" stroke="#262626"/></svg>canyonridge@brivaloka.com</div>
  </div>
  <div class="map" role="img" aria-label="Street map showing the clinic location"></div>
  <h2 style="left:863px">Hours</h2>
  <div class="hours">
    <div class="row"><span>Monday - Thursday:</span><span>9 am - 6 pm</span></div>
    <div class="row"><span>Friday:</span><span>8.30 am - 5 pm</span></div>
    <div class="row"><span>Saturday:</span><span>8.30 am - 5 pm</span></div>
    <div class="row"><span>Closed on</span><span>Sundays</span></div>
    <div class="note">Please keep in mind we are closed<br>for lunch 1-2 pm</div>
  </div>
  <div class="rule"></div>
  <div class="copyright">Copyright © 2015. Company Name. All Right Reserved</div>
  <div class="social"><span></span><span></span><span></span><span></span><span></span></div>
</footer>

</body>
</html>
```